8x8 Social Media Ad - Brant Summit Expo

Attention Real Estate Agents
Please join us for our
Quarterly Real Estate Training Expo
The 2nd Saturday of February, May, August and November
Our Next Training Expo is _________________________________
From 9 am to 1 pm
at
Halvorne Suites Millbrook Court
4817 Copper Willow Lane, Dunmere, MD 20588
Scheduled Speakers
9:00 am - Marcus Pellington - Orientation
9:30 am - Derrin Oakfield - Multiple Income Streams / Crest Program
10:00 am - Talia Brennick - Marketing though Social Media
10:45 am - Rex Dunmore - Generating Business through Ru-Plaza
11:30 am - Kemi Adeyoro - Real Estate Investing
12:15 pm - Gregor Tamsey - (Main Speaker) Training Topic TBA
For more information call Marcus Pellington at (240) 555-0183 or email mpellington@brantsummithomes.example

```html
<!DOCTYPE html>
<html lang="en">
<head>
<meta charset="utf-8">
<title>Brant Summit Expo – Quarterly Real Estate Training Expo</title>
<link href="https://fonts.googleapis.com/css2?family=Barlow+Semi+Condensed:wght@300;400;500;700;800&display=swap" rel="stylesheet">
<style>
  :root {
    --teal: #1597a4;
    --teal-dark: #0d7582;
    --teal-light: #4fb8c2;
    --ink: #1d1d1d;
    --white: #ffffff;
    --backdrop: #d1d2d4;
    --photo-a: #8e9aa0;
    --photo-b: #4c565c;
  }
  * { margin: 0; padding: 0; box-sizing: border-box; }
  html, body { width: 1200px; height: 1010px; overflow: hidden; }
  body {
    background: var(--backdrop);
    font-family: "Barlow Semi Condensed", "Arial Narrow", sans-serif;
    position: relative;
  }
  .ad {
    position: absolute; left: 199px; top: 105px;
    width: 802px; height: 802px;
    background: var(--white);
    overflow: hidden;
  }
  .abs { position: absolute; }

  /* header */
  .header-shapes { position: absolute; left: 0; top: 0; }
  .brand {
    left: 28px; top: 95px; width: 220px;
    display: flex; align-items: center; gap: 8px;
    color: var(--teal-dark); font-weight: 700; font-size: 21px; line-height: 1.05;
    text-transform: uppercase;
  }
  .brand-square { width: 22px; height: 22px; background: var(--teal-dark); flex: none; }
  .headline { right: 49px; text-align: right; text-transform: uppercase; }
  .headline-attention { top: 29px; font-size: 25px; font-weight: 700; color: var(--teal); letter-spacing: .5px; }
  .headline-invite { top: 64px; font-size: 27px; font-weight: 300; color: var(--white); letter-spacing: .5px; }
  .headline-title { top: 94px; font-size: 34px; font-weight: 800; color: var(--white); line-height: 35px; letter-spacing: .3px; }

  /* speakers */
  .section-rule { top: 194px; height: 4px; background: var(--ink); }
  .section-label {
    left: 0; width: 802px; top: 184px; text-align: center;
    font-size: 20px; font-weight: 700; color: var(--ink); letter-spacing: .5px;
  }
  .speakers-backdrop {
    left: 0; top: 213px; width: 802px; height: 390px;
    background: linear-gradient(180deg, var(--teal-light) 0%, var(--teal) 45%, var(--teal-dark) 100%);
  }
  .speaker-bar { background: var(--white); height: 70px; }
  .speaker-time {
    font-size: 19px; font-weight: 700; color: var(--white);
  }
  .speaker-text { color: var(--ink); }
  .speaker-name { font-size: 19px; font-weight: 700; line-height: 20px; }
  .speaker-topic { font-size: 17px; font-weight: 400; line-height: 19px; }
  .speaker-photo {
    width: 110px; height: 110px; border-radius: 50%;
    border: 4px solid var(--white);
    box-shadow: 0 0 0 3px var(--teal-dark);
    background: radial-gradient(circle at 50% 40%, var(--photo-a), var(--photo-b));
  }

  /* details */
  .details-band { left: 0; top: 610px; width: 802px; height: 107px; background: var(--ink); }
  .details-dates {
    left: 32px; top: 624px; font-size: 17px; color: var(--white); text-transform: uppercase; letter-spacing: .2px;
  }
  .details-dates strong { font-weight: 700; }
  .details-rule { left: 28px; top: 651px; width: 744px; height: 1px; background: #8a8a8a; }
  .details-time { left: 32px; top: 667px; font-size: 23px; font-weight: 700; color: var(--white); letter-spacing: .3px; }
  .details-venue {
    left: 252px; top: 660px; font-size: 18px; line-height: 25px; color: var(--white);
    text-transform: uppercase; letter-spacing: .3px;
  }

  /* contact */
  .contact-band { left: 0; top: 723px; width: 802px; height: 79px; background: var(--teal); }
  .contact-lead { left: 32px; top: 735px; font-size: 20px; font-weight: 700; color: var(--white); letter-spacing: .3px; }
  .contact-line { left: 32px; top: 760px; font-size: 20px; color: var(--white); white-space: nowrap; }
  .contact-line strong { font-weight: 700; }
</style>
</head>
<body>
<main class="ad">
  <svg class="header-shapes" width="802" height="180" viewBox="0 0 802 180" aria-hidden="true">
    <polygon points="290,0 802,0 802,23 283,23" fill="var(--teal)"/>
    <polygon points="270,58 802,58 802,179 248,179" fill="var(--teal)"/>
  </svg>

  <div class="abs brand"><span class="brand-square"></span><span>Brant Summit Realty Group</span></div>

  <p class="abs headline headline-attention">Attention Real Estate Agents</p>
  <p class="abs headline headline-invite">Please join us for our</p>
  <h1 class="abs headline headline-title">Quarterly Real Estate<br>Training Expo</h1>

  <div class="abs section-rule" style="left:0;width:283px"></div>
  <div class="abs section-rule" style="left:517px;width:285px"></div>
  <h2 class="abs section-label">SCHEDULED SPEAKERS</h2>

  <div class="abs speakers-backdrop" role="img" aria-label="Photo of a two-storey house with trees, tinted teal"></div>

  <!-- row 1 -->
  <div class="abs speaker-bar" style="left:141px;top:262px;width:259px"></div>
  <div class="abs speaker-bar" style="left:501px;top:260px;width:263px"></div>
  <p class="abs speaker-time" style="left:172px;top:230px">9:00 am</p>
  <p class="abs speaker-time" style="left:553px;top:229px">9:30 am</p>
  <div class="abs speaker-text" style="left:172px;top:268px">
    <p class="speaker-name">Marcus Pellington</p><p class="speaker-topic">Orientation</p>
  </div>
  <div class="abs speaker-text" style="left:553px;top:268px">
    <p class="speaker-name">Derrin Oakfield</p><p class="speaker-topic">Multiple Income<br>Streams / Crest Program</p>
  </div>
  <div class="abs speaker-photo" style="left:43px;top:233px" role="img" aria-label="Portrait of speaker Marcus Pellington"></div>
  <div class="abs speaker-photo" style="left:401px;top:233px" role="img" aria-label="Portrait of speaker Derrin Oakfield"></div>

  <!-- row 2 -->
  <div class="abs speaker-bar" style="left:141px;top:383px;width:259px"></div>
  <div class="abs speaker-bar" style="left:501px;top:383px;width:263px"></div>
  <p class="abs speaker-time" style="left:172px;top:356px">10:00 am</p>
  <p class="abs speaker-time" style="left:551px;top:356px">10:45 am</p>
  <div class="abs speaker-text" style="left:172px;top:388px">
    <p class="speaker-name">Talia Brennick</p><p class="speaker-topic">Marketing though<br>Social Media</p>
  </div>
  <div class="abs speaker-text" style="left:551px;top:388px">
    <p class="speaker-name">Rex Dunmore</p><p class="speaker-topic">Generating Business<br>through Ru-Plaza</p>
  </div>
  <div class="abs speaker-photo" style="left:43px;top:356px" role="img" aria-label="Portrait of speaker Talia Brennick"></div>
  <div class="abs speaker-photo" style="left:404px;top:356px" role="img" aria-label="Portrait of speaker Rex Dunmore"></div>

  <!-- row 3 -->
  <div class="abs speaker-bar" style="left:141px;top:510px;width:259px"></div>
  <div class="abs speaker-bar" style="left:501px;top:510px;width:263px"></div>
  <p class="abs speaker-time" style="left:178px;top:483px">11:30 am</p>
  <p class="abs speaker-time" style="left:554px;top:483px">12:15 pm</p>
  <div class="abs speaker-text" style="left:179px;top:517px">
    <p class="speaker-name">Kemi Adeyoro</p><p class="speaker-topic">Real Estate Investing</p>
  </div>
  <div class="abs speaker-text" style="left:555px;top:517px">
    <p class="speaker-name">Gregor Tamsey</p><p class="speaker-topic">Main Speaker)<br>Training Topic TBA</p>
  </div>
  <div class="abs speaker-photo" style="left:43px;top:481px" role="img" aria-label="Portrait of speaker Kemi Adeyoro"></div>
  <div class="abs speaker-photo" style="left:405px;top:481px" role="img" aria-label="Portrait of speaker Gregor Tamsey"></div>

  <!-- event details -->
  <div class="abs details-band"></div>
  <p class="abs details-dates"><strong>The 2nd Saturday of February, May, August and November</strong> our next training expo is.</p>
  <div class="abs details-rule"></div>
  <p class="abs details-time">FROM 9 AM TO 1 PM</p>
  <p class="abs details-venue">At Halvorne Suites Millbrook Court 4817<br>Copper Willow Lane, Dunmere, MD 20588</p>

  <!-- contact -->
  <div class="abs contact-band"></div>
  <p class="abs contact-lead">FOR MORE INFORMATION CALL</p>
  <p class="abs contact-line">MARCUS PELLINGTON at <strong>(240) 555-0183</strong> or email <strong>mpellington@brantsummithomes.example</strong></p>
</main>
</body>
</html>
```